Commercial/Corporate Law Firm needs Website Design

Hi guys. I've started up a new law firm and would love your help designing an attractive website. I'll need both design and coding, and to make it easy for us to edit as necessary later, I think it should be built off a Wordpress.org structure.
FIRST IMPRESSIONS
It's very important that the first impression of the website really captures our prospective clients' attention and impresses them. Their first three seconds needs to be good.
I imagine the homepage may be short, with a menu bar and a compelling image, and with a tagline overlaid or underneath (eg. "It's about results.")
The image should be related to our practice areas: eg. IPOs, corporate transactions, or commercial negotiations.
I have previously suggested there could be a skyline image of Sydney or Adelaide. However, because we are based in Adelaide, I don't think Sydney is appropriate - and Adelaide is probably too boring to use.
HOMEPAGE
Being a new firm, we don't have many existing testimonials, and I will be the only lawyer to start with. So we need to focus on the nature of the services we will provide and how my experience can help them. We have an existing logo to use, and I would like the website colour scheme not to clash with that logo (dark blue and white).
After the initial image and tagline there should be a brief introduction to each of the main areas of work, eg. "We specialise in three main areas of practice:"
1. Corporate Transactions and Regulation
2. Business Law and Dispute Resolution
3. Migration Assistance
These should each have an appropriate photo and link to a separate page that briefly describes our services in that area.
Below that there should be a message from me with a photo. Finally, at the bottom, there should be a "Contact Us" section which shows a Google image of our address, contact details, and then our logo with colours inverted.
OTHER PAGES
While we will need some other pages, they should all be fairly simple. I think we will need one page to say "About Us", where I will put information about my experience. I think we will then need one page for each of the 3 areas listed above, which just needs an appropriate image and then text to describe the service. Finally, a "Contact Us" page which I imagine will be the same as the bottom of the homepage.
OTHER DETAILS
For now you can use details from my LinkedIn page to fill out any other text as necessary, or the photo.
Because the logo is square, I would prefer the design of the website also to be rectangular.
Looking forward to seeing your work! Thank you.
Marcus
Potential clients:
Businesses with legal issues or disputes
Companies wishing to list on the stock market

```html
<!DOCTYPE html>
<html lang="en">
<head>
<meta charset="utf-8">
<title>Corvane Legal</title>
<link href="https://fonts.googleapis.com/css2?family=Montserrat:wght@400;600;700&family=Lato:wght@400;700&family=Cinzel:wght@700&display=swap" rel="stylesheet">
<style>
:root{
  --navy:#1b3461;
  --blue:#0a62c9;
  --blue-bright:#1766d0;
  --ink:#1d3158;
  --grey:#6b6f76;
  --light:#f4f5f7;
  --white:#fff;
}
*{box-sizing:border-box;margin:0;padding:0}
html,body{width:696px;height:1200px;overflow:hidden}
body{font-family:'Lato',sans-serif;color:var(--grey);background:var(--white);position:relative}
.abs{position:absolute}
.topbar{left:0;top:0;width:696px;height:30px;background:var(--navy)}
.social{left:45px;top:7px;display:flex;gap:4px}
.social span{width:17px;height:17px;border-radius:50%;background:var(--blue-bright);border:1px solid #6f8fc8}
.topcontact{right:81px;top:0;height:30px;display:flex;align-items:center;gap:14px;color:var(--white);font-family:'Montserrat',sans-serif;font-size:9px}
.topcontact div{display:flex;align-items:center;gap:6px}
.header{left:0;top:30px;width:696px;height:79px;background:var(--white)}
.brand{left:45px;top:58px;display:flex;align-items:center;gap:7px}
.brand-square{width:14px;height:14px;background:var(--navy)}
.brand-name{font-family:'Montserrat',sans-serif;font-weight:600;font-size:14px;color:var(--navy);letter-spacing:.5px}
.nav{top:64px;font-family:'Montserrat',sans-serif;font-size:9px;color:var(--grey);letter-spacing:.2px}
.btn-consult{left:530px;top:54px;width:121px;height:29px;background:var(--blue);color:var(--white);font-family:'Montserrat',sans-serif;font-size:9px;display:flex;align-items:center;justify-content:center}
.hero{left:0;top:109px;width:696px;height:332px;background:linear-gradient(100deg,#5c6a78 0%,#9aa3a9 30%,#b9bfc2 55%,#6d7680 80%,#4a525c 100%)}
.hero-title{left:0;width:696px;top:216px;text-align:center;font-family:'Montserrat',sans-serif;font-weight:700;font-size:25px;color:var(--blue-bright)}
.hero-sub{left:0;width:696px;top:248px;text-align:center;font-family:'Montserrat',sans-serif;font-weight:600;font-size:12px;color:var(--white)}
.hero-text{left:198px;width:300px;top:271px;text-align:center;font-size:9px;line-height:14.5px;color:var(--white)}
.btn-contact{left:302px;top:312px;width:91px;height:36px;border-radius:18px;background:var(--blue);color:var(--white);font-family:'Montserrat',sans-serif;font-weight:700;font-size:10.5px;display:flex;align-items:center;justify-content:center}
.dots{left:324px;top:387px;display:flex;gap:8px}
.dots span{width:11px;height:11px;border-radius:50%;border:1.2px solid var(--white)}
.dots .on{background:radial-gradient(var(--white) 40%,transparent 45%)}
.section-title{left:0;width:696px;top:474px;text-align:center;font-family:'Cinzel',serif;font-size:21px;color:var(--ink)}
.section-text{left:138px;width:420px;top:514px;text-align:center;font-family:'Montserrat',sans-serif;font-size:7.5px;line-height:14.5px}
.card{top:586px;width:181px;height:211px;background:var(--white);box-shadow:0 0 8px rgba(0,0,0,.1);text-align:center}
.card svg{position:absolute;left:50%;transform:translateX(-50%);top:26px}
.card h3{position:absolute;top:81px;left:0;width:100%;font-family:'Montserrat',sans-serif;font-weight:700;font-size:11px;line-height:14.5px;color:var(--ink)}
.card .rule{position:absolute;top:120px;left:65px;width:50px;height:1.5px;background:var(--blue)}
.card p{position:absolute;top:135px;left:12px;right:12px;font-size:8px;line-height:14.5px}
.contact-left{left:0;top:846px;width:349px;height:315px;background:var(--blue)}
.contact-right{left:349px;top:846px;width:347px;height:315px;background:radial-gradient(ellipse at 40% 40%,#4a4a4a 0%,#2c2c2c 55%,#1d1d1d 100%)}
.call-label{left:0;width:349px;top:942px;text-align:center;font-family:'Montserrat',sans-serif;font-weight:700;font-size:8px;color:var(--white)}
.phone-box{left:83px;top:966px;width:182px;height:43px;border:1.5px solid var(--white);color:var(--white);font-family:'Montserrat',sans-serif;font-weight:700;font-size:17px;display:flex;align-items:center;justify-content:center}
.divider{left:150px;top:1027px;width:48px;height:1px;background:var(--white)}
.info{top:1050px;width:120px;text-align:center;color:var(--white);font-family:'Montserrat',sans-serif;font-size:7.5px;line-height:14.5px}
.info svg{display:block;margin:0 auto 8px}
.kicker{left:349px;width:347px;top:882px;text-align:center;font-family:'Montserrat',sans-serif;font-size:7.5px;color:var(--white)}
.shout{left:349px;width:347px;top:900px;text-align:center;font-family:'Montserrat',sans-serif;font-weight:600;font-size:20px;color:var(--blue-bright)}
.shout-rule{left:497px;top:936px;width:50px;height:1.5px;background:var(--blue-bright)}
.field{left:395px;width:254px;background:rgba(255,255,255,.55);color:var(--white);font-family:'Montserrat',sans-serif;font-size:7.5px;padding:8px 7px}
.btn-send{left:395px;top:1094px;width:254px;height:30px;background:var(--blue);color:var(--white);font-family:'Montserrat',sans-serif;font-weight:700;font-size:9px;display:flex;align-items:center;justify-content:center}
.footer{left:0;top:1161px;width:696px;height:39px;background:var(--navy);color:var(--white);font-family:'Montserrat',sans-serif;font-size:7.5px;display:flex;align-items:center;justify-content:center}
.footer b{font-weight:700;margin:0 2px}
</style>
</head>
<body>

<div class="abs topbar"></div>
<div class="abs social"><span></span><span></span><span></span></div>
<div class="abs topcontact">
  <div><svg width="13" height="9" viewBox="0 0 13 9"><rect x=".5" y=".5" width="12" height="8" fill="none" stroke="#fff"/><path d="M.5 .5 6.5 5 12.5 .5" fill="none" stroke="#fff"/></svg>info@corvanelegal.com</div>
  <div><svg width="11" height="11" viewBox="0 0 24 24"><path fill="#fff" d="M6.6 10.8a15 15 0 0 0 6.6 6.6l2.2-2.2c.3-.3.7-.4 1-.2 1.1.4 2.3.6 3.6.6.6 0 1 .4 1 1V20c0 .6-.4 1-1 1A17 17 0 0 1 3 4c0-.6.4-1 1-1h3.5c.6 0 1 .4 1 1 0 1.3.2 2.5.6 3.6.1.3 0 .7-.2 1z"/></svg>+1 555 014 2290</div>
</div>

<div class="abs header"></div>
<div class="abs brand"><span class="brand-square"></span><span class="brand-name">CORVANE</span></div>
<div class="abs nav" style="left:213px">HOME</div>
<div class="abs nav" style="left:276px">ABOUT</div>
<div class="abs nav" style="left:343px">PRACTICE AREAS</div>
<div class="abs nav" style="left:452px">CONTACT</div>
<div class="abs btn-consult">FREE CONSULTATION</div>

<div class="abs hero" role="img" aria-label="Photo of a lawyer in a suit meeting a couple at an office desk"></div>
<div class="abs hero-title">ITS ALL ABOUT RESULTS</div>
<div class="abs hero-sub">Help for today,Hope for tomorrow</div>
<div class="abs hero-text">Lorem ipsum dolor sit amet, consectetur adipiscing elit, sed do eiusmod tempor incididunt ut labore et dolore magna aliqua.</div>
<div class="abs btn-contact">CONTACT US</div>
<div class="abs dots"><span></span><span class="on"></span><span></span></div>

<div class="abs section-title">Our Practice Areas</div>
<div class="abs section-text">Lorem ipsum dolor sit amet, consectetur adipiscing elit, sed do eiusmod tempor incididunt ut labore et dolore magna aliqua. Ut enim ad minim veniam, quis nostrud exercitation ullamco laboris nisi ut aliquip ex ea commodo consequat.</div>

<div class="abs card" style="left:45px">
  <svg width="66" height="44" viewBox="0 0 66 44" fill="#0a62c9"><circle cx="15" cy="5" r="4"/><circle cx="33" cy="5" r="4"/><circle cx="51" cy="5" r="4"/><rect x="10" y="11" width="10" height="12" rx="2"/><rect x="28" y="11" width="10" height="12" rx="2"/><rect x="46" y="11" width="10" height="12" rx="2"/><rect x="12" y="20" width="42" height="20"/><path d="M2 14v20h8v8M64 14v20h-8v8" fill="none" stroke="#0a62c9" stroke-width="2"/></svg>
  <h3>Business Law and Dispute<br>Resolution</h3><div class="rule"></div>
  <p>Lorem ipsum dolor sit amet, consectetur adipiscing elit, sed do eiusmod tempor incididunt ut labore et &nbsp;aliqua.</p>
</div>
<div class="abs card" style="left:258px">
  <svg width="44" height="44" viewBox="0 0 44 44" fill="#0a62c9"><path d="M30 0l11 11h-7v16h-8V11h-7z"/><path d="M12 44L1 33h7V19h8v14h7z"/><circle cx="21" cy="21" r="10" fill="#fff" stroke="#0a62c9" stroke-width="2.5"/><text x="21" y="26" font-size="13" text-anchor="middle" font-family="Montserrat,sans-serif" font-weight="700">$</text></svg>
  <h3>Corporate Transactions<br>and Regulation</h3><div class="rule"></div>
  <p>Lorem ipsum dolor sit amet, consectetur adipiscing elit, sed do eiusmod tempor incididunt ut labore et &nbsp;aliqua.</p>
</div>
<div class="abs card" style="left:470px">
  <svg width="48" height="44" viewBox="0 0 48 44"><rect x="18" y="2" width="28" height="40" rx="3" fill="none" stroke="#0a62c9" stroke-width="3.5"/><path d="M8 22h24M24 14l9 8-9 8" fill="none" stroke="#0a62c9" stroke-width="4"/><path d="M2 12h10M2 32h10M6 22h4" stroke="#0a62c9" stroke-width="2"/></svg>
  <h3>Migration<br>Assistance</h3><div class="rule"></div>
  <p>Lorem ipsum dolor sit amet, consectetur adipiscing elit, sed do eiusmod tempor incididunt ut labore et &nbsp;aliqua.</p>
</div>

<div class="abs contact-left"></div>
<svg class="abs" style="left:158px;top:900px" width="32" height="32" viewBox="0 0 24 24"><path fill="#fff" d="M6.6 10.8a15 15 0 0 0 6.6 6.6l2.2-2.2c.3-.3.7-.4 1-.2 1.1.4 2.3.6 3.6.6.6 0 1 .4 1 1V20c0 .6-.4 1-1 1A17 17 0 0 1 3 4c0-.6.4-1 1-1h3.5c.6 0 1 .4 1 1 0 1.3.2 2.5.6 3.6.1.3 0 .7-.2 1z"/></svg>
<div class="abs call-label">Give us a call. 24/7 assistance!</div>
<div class="abs phone-box">+1 555 014 2290</div>
<div class="abs divider"></div>
<div class="abs info" style="left:32px">
  <svg width="12" height="15" viewBox="0 0 12 15"><path d="M6 1a4.5 4.5 0 0 0-4.5 4.5C1.5 9 6 13 6 13s4.5-4 4.5-7.5A4.5 4.5 0 0 0 6 1z" fill="none" stroke="#fff" stroke-width="1.5"/><circle cx="6" cy="5.5" r="1.5" fill="#fff"/><path d="M2 14h8" stroke="#fff"/></svg>
  123,address,city,street<br>name,zipcode</div>
<div class="abs info" style="left:130px">
  <svg width="18" height="15" viewBox="0 0 18 15" fill="#fff"><rect x="5" y="0" width="9" height="5"/><rect x="1" y="5" width="16" height="9" rx="1"/><rect x="0" y="4" width="3" height="11"/></svg>
  123-456-789</div>
<div class="abs info" style="left:229px">
  <svg width="18" height="15" viewBox="0 0 18 15" fill="#fff"><path d="M18 0L0 7l5 2 9-6-7 7v5l3-3 4 3z"/></svg>
  info@corvane.com</div>

<div class="abs contact-right" role="img" aria-label="Dark photo of a justice statue holding scales"></div>
<div class="abs kicker">- CONTACT US -</div>
<div class="abs shout">Give Us a Shout</div>
<div class="abs shout-rule"></div>
<div class="abs field" style="top:955px;height:30px">Name :</div>
<div class="abs field" style="top:991px;height:30px">Email :</div>
<div class="abs field" style="top:1027px;height:60px;padding-top:5px">Message :</div>
<div class="abs btn-send">SEND MESSAGE</div>

<div class="abs footer">© Copyright 2018, <b>CORVANE LEGAL</b>. All rights reserved.</div>

</body>
</html>
```